International IT business needs website revamp.

Velmor Limited would like their current website (www.velmorlimited-example.com) to be revamped/modernized to reflect up-to-date goods and services. Currently, Velmor is offering a conversational AI workflow platform for both enterprise clients and as a DIY solution for SMBs. This platform is called tqFlowbin and allows organizations to automate simple and repetitive workflows to drive their operational efficiency. In addition to the solution offering, Velmor Limited also provides professional IT services. With that said, please use www.velmorlimited-example.com and www.tqflowbin-example.ai for reference of current logos and colourways desired. Furthermore, refer to the attached PDF for a general idea of what to include in the site. The final design should be easy to navigate, clear, concise, and emphasize tqFlowbin as a solution for enterprise clients (while redirecting SMBs to the tqFlowbin website) looking to automate workflow processes/kickstart their digital transformation journey.

```html
<!DOCTYPE html>
<html lang="en">
<head>
<meta charset="utf-8">
<title>Velmor Limited</title>
<link href="https://fonts.googleapis.com/css2?family=Roboto:wght@300;400;500;700;900&display=swap" rel="stylesheet">
<style>
:root{
  --blue:#1a7bc4;
  --blue-dark:#1668a8;
  --teal:#2aa39a;
  --ink:#111;
  --text:#555;
  --grey-bg:#f1f1f1;
  --footer:#1c1c1c;
  --white:#fff;
}
*{margin:0;padding:0;box-sizing:border-box}
html,body{width:1200px;height:3636px;overflow:hidden}
body{position:relative;font-family:'Roboto',sans-serif;color:var(--text);background:var(--white)}
.abs{position:absolute}
a{color:inherit;text-decoration:none}

/* top bar */
.topbar{top:0;left:0;width:1200px;height:34px;background:var(--blue);color:#fff;font-size:12px}
.topbar .item{top:0;height:34px;display:flex;align-items:center;gap:8px}
.topbar .soc{top:9px;width:16px;height:16px;border-radius:50%;background:rgba(255,255,255,.85)}

/* nav */
.nav{top:34px;left:0;width:1200px;height:85px;background:#fff}
.logo{left:110px;top:21px;display:flex;align-items:center;gap:8px;font-size:32px;font-weight:400;color:var(--ink);letter-spacing:1px}
.logo .mark{width:42px;height:42px;border:4px solid var(--ink)}
.menu{left:448px;top:0;height:85px;display:flex;align-items:center;font-size:15px;font-weight:500;color:var(--ink)}
.menu a{position:relative;margin-right:35px}
.menu a.active{color:var(--blue)}
.menu a.active::after{content:"";position:absolute;left:-3px;right:-3px;bottom:-10px;height:3px;background:var(--blue)}
.btn{display:flex;align-items:center;justify-content:center;gap:8px;color:#fff;font-weight:700;border-radius:30px;background:linear-gradient(90deg,#1a6fb8,#2a98b0)}
.btn .dot{width:13px;height:13px;border-radius:50%;background:#fff;position:relative}
.btn .dot::after{content:"";position:absolute;left:3px;top:4px;border:solid var(--blue);border-width:0 2px 2px 0;width:4px;height:4px;transform:rotate(-45deg)}
.demo{left:922px;top:57px;width:166px;height:40px;font-size:15px;font-weight:500}

/* hero */
.hero{top:119px;left:0;width:1200px;height:690px}
.hero svg{position:absolute;left:0;top:0}
.product{left:113px;top:180px;display:flex;align-items:center;gap:12px;font-size:46px;color:#2ea3e6;font-weight:400}
.product .badge{width:50px;height:50px;border-radius:50%;background:#1e6fc2}
.hero-text{left:113px;top:253px;width:480px;color:#fff;font-size:17px;font-weight:500;line-height:28px}
.start{left:113px;top:341px;height:55px;font-size:16px;width:186px}
.arrow{top:260px;width:43px;height:43px;border:2px solid #fff;border-radius:50%}

/* about */
.about{top:809px;left:0;width:1200px;height:559px;background:var(--grey-bg)}
.about-img{left:111px;top:72px;width:398px;height:398px;background:radial-gradient(circle at 55% 45%,#2b9fd8 0%,#0d4f8a 45%,#0a2748 80%);border:1px solid #ddd}
.h2{font-weight:900;color:var(--ink);text-transform:uppercase}
.about h2{left:607px;top:83px;font-size:34px}
.about .copy{left:600px;top:145px;width:488px;font-size:13.5px;line-height:25.6px;color:#555}
.about .copy p{margin-bottom:17px}
.readmore{left:600px;top:399px;width:177px;height:48px;font-size:14px}

/* process */
.process{top:1368px;left:0;width:1200px;height:528px;background:#fff}
.process h2{left:0;width:1200px;text-align:center;top:92px;font-size:33px}
.step{top:205px;width:240px;text-align:center}
.step .icon{width:92px;height:92px;margin:0 auto;border-radius:50%;background:#fff;box-shadow:0 2px 8px rgba(0,0,0,.18);display:flex;align-items:center;justify-content:center}
.step h3{margin-top:20px;font-size:19px;font-weight:500;color:var(--ink)}
.step p{margin-top:12px;font-size:14px;line-height:23.5px;height:70px;overflow:hidden;color:#666}

/* testimonials */
.testi{top:1896px;left:0;width:1200px;height:524px;background:linear-gradient(100deg,#1a6bb6 0%,#2a8fb0 50%,#3aaa8e 100%);color:#fff}
.testi h2{left:0;width:1200px;text-align:center;top:67px;font-size:34px;color:#fff}
.person{top:136px;width:300px;text-align:center}
.person .photo{width:174px;height:174px;margin:0 auto;border-radius:50%;border:3px solid #fff;position:relative}
.person .quote{position:absolute;left:71px;bottom:-12px;width:32px;height:32px;border-radius:50%;background:var(--blue);border:2px solid #fff}
.person .quote::before,.person .quote::after{content:"";position:absolute;top:9px;width:6px;height:9px;background:#fff;border-radius:3px 3px 1px 1px}
.person .quote::before{left:8px}.person .quote::after{left:16px}
.person h3{margin-top:22px;font-size:16px;font-weight:700}
.person .country{font-size:14px;margin-top:2px}
.person p{margin:14px auto 0;width:270px;font-size:15px;line-height:20.5px;height:62px;overflow:hidden}

/* videos */
.videos{top:2420px;left:0;width:1200px;height:550px;background:#fff}
.videos h2{left:0;width:1200px;text-align:center;top:98px;font-size:34px}
.video{top:183px;width:311px;height:267px;color:#fff}
.video .play{position:absolute;left:135px;top:115px;width:40px;height:40px;border:2px solid rgba(255,255,255,.85);border-radius:50%}
.video .play::after{content:"";position:absolute;left:14px;top:10px;border-style:solid;border-width:9px 0 9px 13px;border-color:transparent transparent transparent rgba(255,255,255,.85)}
.video h4{position:absolute;left:22px;top:199px;font-size:17px;font-weight:500}
.video .meta{position:absolute;left:22px;top:230px;font-size:15px;display:flex;gap:26px}
.video .meta span{display:flex;align-items:center;gap:8px}
.video .meta i{display:inline-block;width:13px;height:13px;border-radius:50%;background:#fff}

/* lists */
.lists{top:2970px;left:0;width:1200px;height:406px;background:var(--grey-bg)}
.lists h3{top:76px;font-size:23px;font-weight:700;color:var(--ink)}
.logos{top:133px;width:469px;height:152px;background:#fff;box-shadow:0 2px 8px rgba(0,0,0,.15);display:grid;grid-template-columns:repeat(6,1fr);grid-template-rows:1fr 1fr;align-items:center;justify-items:center;padding:12px 14px}
.name{font-size:21px;font-weight:700;color:#2b2b2b;white-space:nowrap;grid-column:span 2}
.logos .row2{grid-column:span 3}

/* footer */
.footer{top:3376px;left:0;width:1200px;height:260px;background:var(--footer);color:#fff;font-size:13.5px}
.contact{top:40px;display:flex;align-items:center;gap:16px}
.contact .ic{width:46px;height:46px;border-radius:50%;border:2px solid var(--teal);display:flex;align-items:center;justify-content:center}
.contact .lines{line-height:25px}
.rule{left:110px;top:128px;width:979px;height:1px;background:#3a3a3a}
.links{left:110px;top:168px;font-size:13.5px;display:flex;gap:18px}
.copyright{left:110px;top:209px}
.social{top:180px;width:48px;height:48px;border:2px solid #fff;border-radius:50%}
</style>
</head>
<body>

<header>
  <div class="abs topbar">
    <div class="abs item" style="left:628px">
      <svg width="14" height="10" viewBox="0 0 14 10"><rect x="0.5" y="0.5" width="13" height="9" fill="none" stroke="#9fd0f0"/><path d="M1 1l6 5 6-5" fill="none" stroke="#9fd0f0"/></svg>
      <span>info@velmorlimited-example.com</span>
    </div>
    <div class="abs item" style="left:839px">
      <svg width="12" height="12" viewBox="0 0 24 24"><path d="M6.6 10.8a15 15 0 006.6 6.6l2.2-2.2c.3-.3.7-.4 1-.2 1.1.4 2.3.6 3.6.6.6 0 1 .4 1 1V20c0 .6-.4 1-1 1A17 17 0 013 4c0-.6.4-1 1-1h3.5c.6 0 1 .4 1 1 0 1.3.2 2.5.6 3.6.1.3 0 .7-.2 1z" fill="#9fd0f0"/></svg>
      <span>(905) 555-0148</span>
    </div>
    <span class="abs soc" style="left:1007px" aria-label="Social profile"></span>
    <span class="abs soc" style="left:1039px" aria-label="Social profile"></span>
    <span class="abs soc" style="left:1070px" aria-label="Social profile"></span>
  </div>

  <nav class="abs nav">
    <div class="abs logo"><span class="mark"></span>VELMOR</div>
    <div class="abs menu">
      <a class="active">Home</a><a>About Us</a><a>Solution</a><a>Services</a><a>Contact Us</a>
    </div>
  </nav>
  <a class="abs btn demo">Request a Demo <span class="dot"></span></a>
</header>

<section class="abs hero">
  <svg width="1200" height="690" viewBox="0 0 1200 690">
    <defs>
      <radialGradient id="heroGlow" cx="0.7" cy="0.35" r="0.55">
        <stop offset="0" stop-color="#1b5f8f"/>
        <stop offset="0.45" stop-color="#0c2a44"/>
        <stop offset="1" stop-color="#05090f"/>
      </radialGradient>
    </defs>
    <polygon points="0,0 1200,0 1200,576 600,662 0,576" fill="url(#heroGlow)" role="img" aria-label="Glowing digital brain above a circuit board"/>
    <polygon points="0,576 600,662 1200,576 1200,590 600,686 0,590" fill="#1a7bc4"/>
  </svg>
  <div class="abs product"><span class="badge"></span>tqFlowbin</div>
  <p class="abs hero-text">Since 2011, the Velmor team has been providing professional IT services for major Canadian corporations</p>
  <a class="abs btn start">GET STARTED <span class="dot"></span></a>
  <span class="abs arrow" style="left:32px"><svg width="39" height="39" viewBox="0 0 39 39"><path d="M22 12l-7 7.5 7 7.5" fill="none" stroke="#fff" stroke-width="2"/></svg></span>
  <span class="abs arrow" style="left:1128px"><svg width="39" height="39" viewBox="0 0 39 39"><path d="M17 12l7 7.5-7 7.5" fill="none" stroke="#fff" stroke-width="2"/></svg></span>
</section>

<section class="abs about">
  <div class="abs about-img" role="img" aria-label="AI microchip on a glowing circuit board"></div>
  <h2 class="abs h2">About Us</h2>
  <div class="abs copy">
    <p>Since 2011, the Velmor team has been providing professional IT services for major Canadian corporations operating in the telecommunications and financial sectors. As such, our team is highly skilled in technology integration, legacy modernization, system architecture design, application development, quality assurance, project management and more!</p>
    <p>As of 2017, the Velmor team has developed and launched tqFlowbin, a conversational workflow platform powered by AI and ML, into production. Our vision for tqFlowbin is to drive the operational economy,</p>
  </div>
  <a class="abs btn readmore">READ MORE <span class="dot"></span></a>
</section>

<section class="abs process">
  <h2 class="abs h2">The Development Process</h2>
  <div class="abs step" style="left:102px">
    <div class="icon"><svg width="48" height="48" viewBox="0 0 48 48" fill="none" stroke="#1a7bc4" stroke-width="2"><rect x="4" y="6" width="34" height="26"/><circle cx="24" cy="24" r="9"/><path d="M31 31l10 10"/><path d="M10 12h10M10 17h6"/></svg></div>
    <h3>Research</h3>
    <p>Velmor is a competitive player in the IT sector. We will research and apply the latest cutting-edge technologies for you.</p>
  </div>
  <div class="abs step" style="left:353px">
    <div class="icon"><svg width="48" height="48" viewBox="0 0 48 48" fill="none" stroke="#1a7bc4" stroke-width="2"><rect x="5" y="6" width="38" height="28"/><path d="M24 34v8M15 42h18"/><circle cx="15" cy="16" r="5"/><path d="M26 22v-6M31 22v-9M36 22v-4M10 28l8-3 7 2 11-5"/></svg></div>
    <h3>Analysis</h3>
    <p>We will complete a thorough feasibility study to identify and understand exactly what you need from the project.</p>
  </div>
  <div class="abs step" style="left:603px">
    <div class="icon"><svg width="48" height="48" viewBox="0 0 48 48" fill="none" stroke="#1a7bc4" stroke-width="2"><rect x="5" y="8" width="38" height="26"/><path d="M24 34v7M15 41h18"/><rect x="12" y="13" width="24" height="14"/><path d="M17 24v-5M22 24v-7M27 24v-4M32 24v-6"/></svg></div>
    <h3>Design</h3>
    <p>Work with us every step of the way as we perform a prototype architecture design to develop an ideal solution.</p>
  </div>
  <div class="abs step" style="left:854px">
    <div class="icon"><svg width="48" height="48" viewBox="0 0 48 48" fill="none" stroke="#1a7bc4" stroke-width="2"><path d="M9 4h20l8 8v32H9z"/><path d="M29 4v8h8"/><path d="M14 16h12M14 21h16"/><path d="M16 38v-6M21 38v-9M26 38v-4M31 38v-7"/><path d="M41 14v22l-2 4-2-4V14z"/></svg></div>
    <h3>Delivery</h3>
    <p>Velmor offers comprehensive services including system integration, maintenance, and ongoing support for clients.</p>
  </div>
</section>

<section class="abs testi">
  <h2 class="abs h2">Testimonials</h2>
  <div class="abs person" style="left:121px">
    <div class="photo" style="background:linear-gradient(160deg,#e9e4df,#b9a89a)" role="img" aria-label="Portrait of a smiling client representative"><span class="quote"></span></div>
    <h3>NORTHGATE</h3><div class="country">Canada</div>
    <p>Naturally, the Northgate website receives thousands of visitors a day. As a result, we noticed the need to automate our support.</p>
  </div>
  <div class="abs person" style="left:450px">
    <div class="photo" style="background:linear-gradient(160deg,#dcdcdc,#4a4f57)" role="img" aria-label="Portrait of a client representative in a suit"><span class="quote"></span></div>
    <h3>CIVICLINE</h3><div class="country">Canada</div>
    <p>Leveraging tqFlowbin's extremely user-friendly interface, Civicline was able to build and implement our workflows.</p>
  </div>
  <div class="abs person" style="left:779px">
    <div class="photo" style="background:linear-gradient(160deg,#f0f0f0,#3c3f46)" role="img" aria-label="Portrait of a client executive in a suit"><span class="quote"></span></div>
    <h3>HARBOURVIEW HOMES</h3><div class="country">Canada</div>
    <p>Our company, Harbourview Homes, was able to deploy our salesbot instance within one month! We were extremely pleased.</p>
  </div>
</section>

<section class="abs videos">
  <h2 class="abs h2">Promotional Videos</h2>
  <div class="abs video" style="left:111px;background:linear-gradient(160deg,#9aa3ad,#4d5561 60%,#2b3038)" role="img" aria-label="Business team in a meeting">
    <span class="play"></span><h4>Lorem ipsum dolor sit</h4>
    <div class="meta"><span><i></i>2h | 30m</span><span><i></i>2536</span></div>
  </div>
  <div class="abs video" style="left:445px;background:linear-gradient(160deg,#c9c4bd,#6b6660 55%,#2c2a28)" role="img" aria-label="Presenter showing a chart to colleagues">
    <span class="play"></span><h4>Lorem ipsum dolor sit</h4>
    <div class="meta"><span><i></i>2h | 30m</span><span><i></i>2536</span></div>
  </div>
  <div class="abs video" style="left:778px;background:linear-gradient(160deg,#aab8cc,#5f6f86 55%,#323c4c)" role="img" aria-label="Hands typing on a laptop with a digital brain overlay">
    <span class="play"></span><h4>Lorem ipsum dolor sit</h4>
    <div class="meta"><span><i></i>2h | 30m</span><span><i></i>2536</span></div>
  </div>
</section>

<section class="abs lists">
  <h3 class="abs" style="left:109px">LIST OF CLIENT</h3>
  <h3 class="abs" style="left:620px">LIST OF PARTNERS</h3>
  <div class="abs logos" style="left:109px">
    <span class="name">Kestrel Tel</span>
    <span class="name">Maplecrest</span>
    <span class="name">Lumora</span>
    <span class="name row2">Fintrove</span>
    <span class="name row2">Corvane</span>
  </div>
  <div class="abs logos" style="left:620px">
    <span class="name">Halvex</span>
    <span class="name">Stonemill</span>
    <span class="name">Quorra</span>
    <span class="name row2">Brightwell</span>
    <span class="name row2">Tamarind</span>
  </div>
</section>

<footer class="abs footer">
  <div class="abs contact" style="left:240px">
    <span class="ic"><svg width="16" height="20" viewBox="0 0 16 20"><path d="M8 1a7 7 0 00-7 7c0 5 7 11 7 11s7-6 7-11a7 7 0 00-7-7z" fill="none" stroke="#2aa39a" stroke-width="2"/><circle cx="8" cy="8" r="2.5" fill="#2aa39a"/></svg></span>
    <div class="lines">120 Harbour Lane, Unit 4 &amp; 5<br>&nbsp;Lakefield, ON Canada, K0L 2H0</div>
  </div>
  <div class="abs contact" style="left:560px">
    <span class="ic"><svg width="18" height="18" viewBox="0 0 24 24"><path d="M6.6 10.8a15 15 0 006.6 6.6l2.2-2.2c.3-.3.7-.4 1-.2 1.1.4 2.3.6 3.6.6.6 0 1 .4 1 1V20c0 .6-.4 1-1 1A17 17 0 013 4c0-.6.4-1 1-1h3.5c.6 0 1 .4 1 1 0 1.3.2 2.5.6 3.6.1.3 0 .7-.2 1z" fill="#2aa39a"/></svg></span>
    <div class="lines">(905) 555-0148</div>
  </div>
  <div class="abs contact" style="left:740px">
    <span class="ic"><svg width="18" height="13" viewBox="0 0 18 13"><rect x="1" y="1" width="16" height="11" fill="none" stroke="#2aa39a" stroke-width="2"/><path d="M1 1l8 6 8-6" fill="none" stroke="#2aa39a" stroke-width="2"/></svg></span>
    <div class="lines">info@velmorlimited-example.com</div>
  </div>
  <div class="abs rule"></div>
  <div class="abs links">
    <a>Help</a><span>|</span><a>FAQ</a><span>|</span><a>Support</a><span>|</span><a>Sitemap</a><span>|</span><a>Terms &amp; Conditions</a><span>|</span><a>Privacy Statement</a>
  </div>
  <div class="abs copyright">velmorlimited © 2020 All rights reserved.</div>
  <span class="abs social" style="left:864px" aria-label="Social profile"></span>
  <span class="abs social" style="left:922px" aria-label="Social profile"></span>
  <span class="abs social" style="left:981px" aria-label="Social profile"></span>
  <span class="abs social" style="left:1040px" aria-label="Social profile"></span>
</footer>

</body>
</html>
```